Maris Dovey Studio Business Cards

Hi - using the information and logo provided I require a two sided business card designed with the following information. The business card is a 'mini card' 3.5" x 1.25".

Front of card should be the logo attached but inverted (so the background is the peach colour and the logo white).

Back should have these details. If we can't fit the Pictogrum and Friendwall part can we just put the little logos.

Tessa Varnold

Art and Design Consultant
Dealer - Curator - Events - Styling - Creative Sourcing

P: 0438 217 604
E: tessa@marisdoveystudio.example
W: www.marisdoveystudio.example
I (pictogram image please): marisdoveystudio F (Friendwall image please): MarisDoveyAdviser

Target Market(s)

Galleries, artists, art buyers, interior design clients, event managers, creative types

Industry/Entity Type

Business

```html
<!DOCTYPE html>
<html lang="en">
<head>
<meta charset="utf-8">
<title>Maris Dovey Studio – Business Cards</title>
<link rel="stylesheet" href="https://fonts.googleapis.com/css2?family=Libre+Baskerville&family=Lora&family=Montserrat:wght@400&family=Arimo&display=swap">
<style>
  :root {
    --backdrop: #8e8e8e;
    --peach: #f5bc9f;
    --peach-text: #f2b393;
    --paper: #f3f3f5;
    --ink: #6a6b70;
    --ink-soft: #858589;
    --white: #ffffff;
    --rule: #cfcfd3;
  }
  * { margin: 0; padding: 0; box-sizing: border-box; }
  html, body { width: 1200px; height: 988px; overflow: hidden; }
  body { background: var(--backdrop); position: relative; }

  .card {
    position: absolute;
    left: 86px;
    width: 1029px;
    height: 366px;
    text-align: center;
  }
  .card--front { top: 102px; background: var(--peach); }
  .card--back  { top: 537px; background: var(--paper); }

  /* front */
  .brand-mark {
    position: absolute;
    left: 50%;
    top: 128px;
    width: 84px;
    height: 84px;
    margin-left: -42px;
    border-radius: 50%;
    background: var(--white);
  }
  .brand-name {
    position: absolute;
    left: 0; right: 0;
    top: 240px;
    font-family: "Libre Baskerville", serif;
    font-size: 36px;
    letter-spacing: 6px;
    color: var(--white);
    line-height: 1;
  }

  /* back */
  .person-name {
    position: absolute; left: 0; right: 0; top: 48px;
    font-family: "Lora", serif;
    font-size: 46px;
    color: var(--peach-text);
    line-height: 1;
  }
  .person-role {
    position: absolute; left: 0; right: 0; top: 110px;
    font-family: "Lora", serif;
    font-size: 25px;
    color: var(--ink-soft);
    line-height: 1;
  }
  .services {
    position: absolute; left: 0; right: 0; top: 146px;
    font-family: "Lora", serif;
    font-size: 28px;
    letter-spacing: 0.5px;
    color: var(--ink-soft);
    line-height: 1;
  }
  .divider {
    position: absolute; left: 39px; right: 31px; top: 213px;
    height: 2px; background: var(--rule);
  }
  .socials {
    position: absolute; left: 0; right: 0; top: 242px;
    display: flex; justify-content: center; gap: 30px;
    font-family: "Arimo", sans-serif;
    font-size: 26px;
    color: var(--ink);
    line-height: 1;
  }
  .social { display: flex; align-items: center; gap: 10px; }
  .social__icon {
    width: 30px; height: 30px;
    background: var(--peach); border-radius: 4px;
  }
  .contact {
    position: absolute; left: 0; right: 0; top: 300px;
    font-family: "Arimo", sans-serif;
    font-size: 26px;
    color: var(--ink);
    line-height: 1;
  }
</style>
</head>
<body>
  <section class="card card--front" aria-label="Card front">
    <div class="brand-mark"></div>
    <p class="brand-name">MARIS DOVEY STUDIO</p>
  </section>

  <section class="card card--back" aria-label="Card back">
    <h1 class="person-name">Tessa Varnold</h1>
    <p class="person-role">Art and Design Consultant</p>
    <p class="services">DEALER - CURATOR - EVENTS - STYLING - CREATIVE SOURCING</p>
    <div class="divider"></div>
    <div class="socials">
      <span class="social"><span class="social__icon"></span>marisdoveystudio</span>
      <span class="social"><span class="social__icon"></span>MarisDoveyAdviser</span>
    </div>
    <p class="contact">0438 217 604 | tessa@marisdoveystudio.example | www.marisdoveystudio.example</p>
  </section>
</body>
</html>
```